SkyvornQ Business Cards and Stationary Design

Need a design for our business cards and stationary. I want to carry on the theme of the logo. I want the business cards to have a design on the back. I would like the business cards and the stationary to carry the same theme, design scheme, and branding

Target Market(s)

Airlines and Maintenance Facilities

Industry/Entity Type

Aviation

Contact Information for Business Card

Name
Position Title
Address: 4827 Trellis Hollow Road, Fort Pierce, Florida, 34951
Office Number
Mobile Number
Email
Website

Font styles to use
Serif
Sans Serif

Colors

Designer to choose colors to be used in the design.

```html
<!DOCTYPE html>
<html lang="en">
<head>
<meta charset="utf-8">
<title>SkyvornQ Business Card</title>
<link href="https://fonts.googleapis.com/css2?family=Open+Sans:wght@300;400;700&display=swap" rel="stylesheet">
<style>
  :root {
    --backdrop: #dcdddf;
    --card: #ffffff;
    --navy: #1c2f5e;
    --navy-deep: #152548;
    --sky: #2a8fd0;
    --ink: #2b2b2b;
    --rule: #c9c9c9;
    --edge: #3a3a3a;
  }
  * { margin: 0; padding: 0; box-sizing: border-box; }
  html, body {
    width: 1200px; height: 1103px; overflow: hidden;
    background: var(--backdrop);
    font-family: "Open Sans", Arial, sans-serif;
    color: var(--ink);
  }
  .canvas { position: relative; width: 1200px; height: 1103px; }
  .card {
    position: absolute;
    width: 789px; height: 450px;
    background: var(--card);
    border: 1px solid var(--edge);
    border-radius: 40px;
    overflow: hidden;
  }
  .card--front { left: 62px; top: 70px; }
  .card--back { left: 358px; top: 574px; }

  .swoosh { position: absolute; inset: 0; width: 100%; height: 100%; }

  .holder {
    position: absolute; right: 45px; top: 38px;
    text-align: right; color: #fff;
  }
  .holder__name { font-weight: 700; font-size: 25px; letter-spacing: 0.3px; line-height: 1.3; }
  .holder__title { font-weight: 300; font-size: 23px; line-height: 1.25; }

  .brand-dot {
    position: absolute;
    border-radius: 50%;
    background: var(--sky);
  }
  .card--front .brand-dot { left: 168px; top: 72px; width: 122px; height: 122px; }
  .card--back .brand-dot { left: 321px; top: 93px; width: 144px; height: 144px; }

  .wordmark {
    position: absolute;
    font-family: "Open Sans", Arial, sans-serif;
    font-weight: 700;
    color: var(--navy-deep);
    line-height: 1;
    white-space: nowrap;
  }
  .card--front .wordmark { left: 40px; top: 224px; font-size: 44px; }
  .card--back .wordmark { left: 0; right: 0; top: 256px; font-size: 48px; text-align: center; }

  .contact { position: absolute; font-size: 17.5px; line-height: 28px; }
  .contact li { list-style: none; display: flex; align-items: center; gap: 4px; }
  .contact svg { width: 18px; height: 18px; flex: none; }
  .contact--direct { left: 40px; top: 306px; }
  .contact--address { left: 290px; top: 362px; }
  .contact--address li { align-items: flex-start; }
  .contact--address svg { margin-top: 5px; }
  .divider {
    position: absolute; left: 265px; top: 366px;
    width: 2px; height: 50px; background: var(--rule);
  }
  .site {
    position: absolute; left: 0; right: 0; top: 366px;
    text-align: center; font-size: 22px; letter-spacing: 5px; color: var(--ink);
  }
</style>
</head>
<body>
<div class="canvas">

  <section class="card card--front">
    <svg class="swoosh" viewBox="0 0 737 421" preserveAspectRatio="none" aria-hidden="true">
      <defs>
        <radialGradient id="bandGlow" cx="0.55" cy="0.15" r="0.6">
          <stop offset="0" stop-color="#2a93d4"/>
          <stop offset="0.55" stop-color="#235d98"/>
          <stop offset="1" stop-color="#1c2f5e"/>
        </radialGradient>
      </defs>
      <path d="M0 0 H737 V210 C600 150 420 62 250 36 C150 22 60 30 0 68 Z" fill="url(#bandGlow)"/>
      <path d="M0 78 C60 38 150 30 250 44 C420 70 600 162 737 222 V252 C600 188 420 88 250 54 C150 40 60 46 0 86 Z" fill="#152548"/>
    </svg>

    <div class="holder">
      <p class="holder__name">MARLOW KESTRANE</p>
      <p class="holder__title">PRESIDENT</p>
    </div>

    <span class="brand-dot" aria-hidden="true"></span>
    <p class="wordmark">SkyvornQ</p>

    <ul class="contact contact--direct">
      <li>
        <svg viewBox="0 0 18 18"><circle cx="9" cy="9" r="7.5" fill="none" stroke="#1c2f5e" stroke-width="1.4"/><path d="M6 5.2 7.4 5 8.2 7 7.3 7.8C7.8 9 8.9 10.2 10.2 10.7L11 9.8 13 10.6 12.8 12C9 12.6 5.2 8.8 6 5.2Z" fill="#1c2f5e"/></svg>
        012-345-6789
      </li>
      <li>
        <svg viewBox="0 0 18 18"><circle cx="9" cy="9" r="7.5" fill="none" stroke="#1c2f5e" stroke-width="1.4"/><rect x="6.3" y="4.5" width="5.4" height="9" rx="1" fill="none" stroke="#1c2f5e" stroke-width="1.3"/></svg>
        012-345-6789
      </li>
      <li>
        <svg viewBox="0 0 18 18"><circle cx="9" cy="9" r="7.5" fill="none" stroke="#1c2f5e" stroke-width="1.4"/><rect x="5" y="6.2" width="8" height="5.8" fill="#1c2f5e"/><path d="M5 6.4 9 9.4 13 6.4" fill="none" stroke="#fff" stroke-width="1"/></svg>
        info@skyvornq.com
      </li>
      <li>
        <svg viewBox="0 0 18 18"><g fill="none" stroke="#1c2f5e" stroke-width="1.3"><circle cx="9" cy="9" r="7.5"/><ellipse cx="9" cy="9" rx="3.3" ry="7.5"/><path d="M1.5 9H16.5M3 5H15M3 13H15"/></g></svg>
        www.skyvornq.com
      </li>
    </ul>

    <span class="divider"></span>

    <ul class="contact contact--address">
      <li>
        <svg viewBox="0 0 18 18"><circle cx="9" cy="9" r="7.5" fill="none" stroke="#1c2f5e" stroke-width="1.4"/><path d="M9 13.5C7 11 6 9.5 6 8A3 3 0 0 1 12 8C12 9.5 11 11 9 13.5Z" fill="#1c2f5e"/><circle cx="9" cy="8" r="1.1" fill="#fff"/></svg>
        <span>123, Street Name, City Name<br>Zipcode-012345</span>
      </li>
    </ul>
  </section>

  <section class="card card--back">
    <span class="brand-dot" aria-hidden="true"></span>
    <p class="wordmark">SkyvornQ</p>
    <p class="site">www.skyvornq.com</p>
  </section>

</div>
</body>
</html>
```